Label design for an exciting new Vodka brand

We need a label design for a dynamic new Vodka brand called 'Pale lantern drift Vodka'. It is a crisp and versatile liquid with a clean and smooth finish. It should appeal to 21-39 year olds, with a slight female skew. Colours, fonts and styles should be modern and relatively neutral - take inspiration from the brand pictures attached.

Target Market(s)

21-39 year olds, both male and female, but with a slight female skew

```html
<!DOCTYPE html>
<html lang="en">
<head>
<meta charset="utf-8">
<title>Pale lantern drift Vodka — Label</title>
<link href="https://fonts.googleapis.com/css2?family=Fraunces:opsz,wght@9..144,800&family=Montserrat:wght@700&display=swap" rel="stylesheet">
<style>
  :root {
    --canvas: #ffffff;
    --label-peach: #f7dcc4;
    --label-peach-deep: #f1cfb2;
    --brand-red: #e63a30;
    --gold-light: #f3d36b;
    --gold-deep: #c7801f;
  }
  * { box-sizing: border-box; margin: 0; padding: 0; }
  html, body {
    width: 1200px; height: 1200px; overflow: hidden;
    background: var(--canvas);
  }
  .canvas {
    position: relative; width: 1200px; height: 1200px;
  }
  .label {
    position: absolute; left: 180px; top: 40px;
    width: 840px; height: 1120px;
    background: var(--label-peach);
    overflow: hidden;
  }
  .label-texture {
    position: absolute; inset: 0;
    background: linear-gradient(180deg, var(--label-peach) 0%, var(--label-peach-deep) 50%, var(--label-peach) 100%);
  }
  .gold-frame {
    position: absolute; left: 20px; top: 26px; right: 20px; bottom: 26px;
    border-radius: 20px;
    border: 4px solid var(--gold-deep);
    box-shadow: inset 0 0 0 1px var(--gold-light);
  }
  .brand-dot {
    position: absolute; left: 300px; top: 305px;
    width: 240px; height: 240px; border-radius: 50%;
    background: var(--brand-red);
  }
  .brand-name {
    position: absolute; left: 0; right: 0; top: 790px;
    text-align: center;
    font-family: "Fraunces", Georgia, serif;
    font-weight: 800;
    font-size: 78px;
    line-height: 1;
    letter-spacing: -1px;
    color: var(--brand-red);
    white-space: nowrap;
  }
  .product-type {
    position: absolute; left: 0; right: 0; top: 932px;
    text-align: center;
    font-family: "Montserrat", Arial, sans-serif;
    font-weight: 700;
    font-size: 50px;
    line-height: 1;
    letter-spacing: 1px;
    color: var(--brand-red);
  }
</style>
</head>
<body>
<main class="canvas">
  <section class="label">
    <div class="label-texture" role="img" aria-label="Faint tone-on-tone text texture across the label background"></div>
    <div class="gold-frame"></div>
    <div class="brand-dot" aria-hidden="true"></div>
    <h1 class="brand-name">Pale lantern drift</h1>
    <p class="product-type">VODKA</p>
  </section>
</main>
</body>
</html>
```